Transform Your Giving

I need a tri-fold brochure that will fit in a standard number 10 business envelope. Meadowlark and Allied Services is a charitable nonprofit. The goal of this brochure is to stimulate people into thinking about other ways to make a donation. The design should communicate the essential information on donation options, create a sense of professional integrity, be graphically sharp, easy to read and laid out in a way that doesn't make the material appear crowded.

```html
<!DOCTYPE html>
<html lang="en">
<head>
<meta charset="utf-8">
<title>Transform Your Giving – Tri-fold Brochure</title>
<link rel="stylesheet" href="https://fonts.googleapis.com/css2?family=Bebas+Neue&family=Montserrat:ital,wght@0,400;0,500;0,600;0,700;0,800;1,600;1,700&display=swap">
<style>
:root{
  --page:#e9e9e9;
  --purple:#2f2783;
  --purple-light:#4a3aa3;
  --navy:#24205e;
  --green:#43b02a;
  --green-bright:#5cc43a;
  --white:#ffffff;
  --ink:#222222;
  --head:'Bebas Neue', sans-serif;
  --body:'Montserrat', sans-serif;
}
*{box-sizing:border-box;margin:0;padding:0}
html,body{width:720px;height:1200px;overflow:hidden}
body{background:var(--page);font-family:var(--body);color:var(--ink);position:relative}
.sheet{position:absolute;left:60px;width:595px;height:460px;background:var(--white);box-shadow:0 1px 4px rgba(0,0,0,.18);overflow:hidden}
.sheet--outside{top:110px}
.sheet--inside{top:651px}
.panel{position:absolute;top:0;width:199px;height:460px;overflow:hidden}
.panel--1{left:0}.panel--2{left:198px}.panel--3{left:397px;width:198px}
.panel--purple{background:linear-gradient(135deg,var(--purple-light) 0%,var(--purple) 45%,#2a2170 100%);color:var(--white)}
.abs{position:absolute}
.photo{position:absolute}
.curve{position:absolute;left:0;top:0}
p{font-size:5.8px;line-height:7.2px}
.center{text-align:center}

/* outside panel 1 */
.impact-title{position:absolute;left:0;top:305px;height:20px;width:137px;background:var(--purple);border-radius:0 10px 10px 0;color:var(--white);font-family:var(--head);font-weight:400;font-size:15px;line-height:21px;padding-left:14px;letter-spacing:.2px;white-space:nowrap}
.impact-copy{position:absolute;left:14px;top:337px;width:178px}
.checklist{position:absolute;left:14px;top:390px;list-style:none}
.checklist li{font-size:5.8px;font-weight:500;height:12.8px;display:flex;align-items:center;gap:5px}
.tick{width:5px;height:5px;border:.6px solid #555;position:relative;flex:none}
.tick::after{content:"";position:absolute;left:1px;top:0;width:1.6px;height:2.6px;border:solid #555;border-width:0 .6px .6px 0;transform:rotate(45deg)}

/* outside panel 2 */
.intro-note{position:absolute;left:14px;top:14px;width:171px}
.quote{position:absolute;left:18px;top:58px;width:164px;height:62px}
.quote-text{position:absolute;left:2px;top:20px;font-size:7.2px;line-height:9px;font-style:italic;color:var(--white)}
.quote-text b{font-weight:700}
.quote-mark{position:absolute;font-family:Georgia,serif;font-weight:700;color:var(--green);font-size:38px;line-height:1}
.brand-name{font-family:var(--body);font-weight:700;color:var(--white);text-align:center}
.brand-name--mid{position:absolute;left:10px;top:140px;width:179px;font-size:9.5px;line-height:12px}
.brand-dot{display:block;margin:0 auto 4px;width:8px;height:8px;border-radius:50%;background:var(--green)}
.will-pill{position:absolute;left:26px;top:191px;width:148px;height:29px;border-radius:9px;background:linear-gradient(180deg,var(--green-bright),var(--green));color:var(--white);text-align:center;font-size:5.6px;line-height:7.2px;padding-top:3.5px;box-shadow:0 0 8px rgba(255,255,255,.25)}
.will-pill b{font-weight:700}
.contact-head{position:absolute;left:0;width:199px;top:245px;text-align:center;font-weight:700;font-size:7.3px;text-decoration:underline;letter-spacing:.2px}
.contact-lead{position:absolute;left:0;width:199px;top:261px}
.contact-item{position:absolute;left:0;width:199px;text-align:center}
.c-icon{display:block;margin:0 auto 2px;width:8px;height:8px;border-radius:50%;background:var(--green)}
.c-icon svg{display:block}
.follow-head{position:absolute;left:0;width:199px;top:389px;text-align:center;font-weight:700;font-size:7.3px;text-decoration:underline}
.social{position:absolute;left:71px;top:401px;width:57px;height:10px}
.social span{position:absolute;top:0;width:10px;height:10px;border-radius:50%;background:var(--green)}
.disclaimer{position:absolute;left:18px;top:428px;width:163px;font-size:3.4px;line-height:4.3px;text-align:center}

/* outside panel 3 – cover */
.cover-title{position:absolute;left:0;width:198px;top:12px;text-align:center;font-family:var(--head);font-weight:400;font-size:23.5px;line-height:24px;color:var(--green);letter-spacing:-.1px;white-space:nowrap}
.cover-pill{position:absolute;left:21px;top:35px;width:157px;height:14px;border-radius:8px;background:var(--navy);color:var(--white);font-weight:800;font-size:10.3px;line-height:14px;text-align:center;letter-spacing:.3px;white-space:nowrap}
.cover-sub{position:absolute;left:0;width:198px;top:53px;text-align:center;font-size:8px;line-height:10px;color:#333}
.bubble{position:absolute;width:48px;height:48px;border-radius:50%;background:radial-gradient(circle at 35% 30%,#ffffff 0%,#f2f1f8 55%,#cfcde0 100%);box-shadow:0 1px 3px rgba(0,0,0,.3);text-align:center;color:var(--navy);font-size:5.4px;font-weight:600;line-height:5.8px}
.bubble svg{display:block;margin:8px auto 2px}
.brand-name--cover{position:absolute;left:0;top:407px;width:198px;color:var(--navy);font-size:10px;line-height:12px}
.brand-name--cover .brand-dot{margin-bottom:5px}

/* inside panels */
.feature-head{position:absolute;display:flex;gap:6px}
.feature-icon{flex:none}
.feature-title{font-weight:700;font-size:7.6px;line-height:8.8px;color:var(--green)}
.feature-tag{font-weight:700;font-style:italic;font-size:5.6px;line-height:7px;color:var(--green);margin-top:1px}
.how-pill{position:absolute;height:11px;padding:0 5px;background:var(--green);color:var(--white);font-weight:700;font-size:7px;line-height:11px;letter-spacing:.3px;border-radius:2px 6px 6px 2px;white-space:nowrap}
.copy{position:absolute;width:172px}
.bullets{position:absolute;left:14px;width:170px;list-style:none}
.bullets li{display:flex;gap:6px;font-size:5.8px;line-height:7.2px;margin-bottom:6px}
.bullets .tick{border-color:#fff;margin-top:1px}
.bullets .tick::after{border-color:#fff}
.url-pill{position:absolute;right:0;top:436px;height:12px;width:122px;padding:0 6px;background:var(--navy);border-radius:7px 0 0 7px;color:var(--white);font-size:7.4px;line-height:12px;text-align:center;white-space:nowrap}
.panel--white .copy{color:#222}
</style>
</head>
<body>

<!-- OUTSIDE SHEET -->
<section class="sheet sheet--outside">

  <div class="panel panel--1">
    <div class="photo" style="left:0;top:0;width:199px;height:300px;background:linear-gradient(160deg,#ecebe9 0%,#d9d4cd 45%,#b9aea2 75%,#8e8679 100%)" role="img" aria-label="Photo of a younger woman comforting a distressed older woman on a sofa"></div>
    <svg class="curve" width="199" height="460" viewBox="0 0 199 460" aria-hidden="true">
      <path d="M0 282 Q95 238 199 328 L199 460 L0 460 Z" fill="#ffffff"/>
      <path d="M0 282 Q95 238 199 328 L199 316 Q95 220 0 276 Z" fill="var(--green)"/>
    </svg>
    <h2 class="impact-title">THE IMPACT OF YOUR GIFT</h2>
    <p class="impact-copy">Your generosity drives our mission. With every Smart gift you're supporting Meadowlark and Allied Services. Join our community of Smart Givers today and make an enduring impact. With Smart Giving your generosity reaches further. Begin your Smart Giving journey with us today.</p>
    <ul class="checklist">
      <li><span class="tick"></span>Stocks and Securities</li>
      <li><span class="tick"></span>DAFs</li>
      <li><span class="tick"></span>QCDs</li>
      <li><span class="tick"></span>Crypto</li>
      <li><span class="tick"></span>Charitable Annuity</li>
    </ul>
  </div>

  <div class="panel panel--2 panel--purple">
    <p class="intro-note center">To learn more about Smart Giving Options and how they can benefit you and Meadowlark and Allied Services, please reach out to our team. We're here to help you navigate these giving methods and answer any question you may have.</p>
    <div class="quote">
      <svg class="abs" style="left:12px;top:0" width="152" height="50" viewBox="0 0 152 50" aria-hidden="true">
        <path d="M18 11 H144 Q150 11 150 17 V37 Q150 43 144 43 H98" fill="none" stroke="var(--green)" stroke-width=".7"/>
      </svg>
      <span class="quote-mark" style="left:0;top:-4px">&ldquo;</span>
      <p class="quote-text">Being kind to others is a way of being<br>good to yourself.<br><b>- Ellen Marsh</b></p>
      <span class="quote-mark" style="left:74px;top:34px">&rdquo;</span>
    </div>
    <div class="brand-name brand-name--mid"><span class="brand-dot"></span>Meadowlark and Allied Services</div>
    <div class="will-pill">If you do not have a will, go to<br><b>www.easywillnow.org</b><br>In 20 minutes you can have a legal will for free.</div>
    <h3 class="contact-head">CONTACT US</h3>
    <p class="contact-lead center">Have more question?<br>Please contact us at Meadowlark &amp; Allied Services</p>
    <div class="contact-item" style="top:281px">
      <span class="c-icon"><svg width="8" height="8" viewBox="0 0 8 8"><path d="M4 1.6a1.5 1.5 0 0 1 1.5 1.5C5.5 4.3 4 6.3 4 6.3S2.5 4.3 2.5 3.1A1.5 1.5 0 0 1 4 1.6z" fill="#fff"/></svg></span>
      <p>1420 Prairie View Rd.<br>Suite 4, Fargo, ND 58102</p>
    </div>
    <div class="contact-item" style="top:308px">
      <span class="c-icon"><svg width="8" height="8" viewBox="0 0 8 8"><path d="M2.4 2c.4-.3.7 0 .9.4l.3.7c.1.3-.2.5-.3.7.3.6.8 1.1 1.4 1.4.2-.1.4-.4.7-.3l.7.3c.4.2.7.5.4.9-.6.7-1.6.4-2.6-.4S1.7 2.6 2.4 2z" fill="#fff"/></svg></span>
      <p>555-014-2200 (ext. 100)</p>
    </div>
    <div class="contact-item" style="top:330px">
      <span class="c-icon"><svg width="8" height="8" viewBox="0 0 8 8"><rect x="2" y="2.7" width="4" height="2.8" fill="#fff"/><path d="M2 2.7L4 4.3 6 2.7" fill="none" stroke="var(--green)" stroke-width=".4"/></svg></span>
      <p>info@meadowlarkallied.org</p>
    </div>
    <div class="contact-item" style="top:352px">
      <span class="c-icon"><svg width="8" height="8" viewBox="0 0 8 8"><circle cx="4" cy="4" r="2" fill="none" stroke="#fff" stroke-width=".5"/><path d="M2 4h4M4 2v4" stroke="#fff" stroke-width=".4"/></svg></span>
      <p>www.meadowlarkallied.org</p>
    </div>
    <h3 class="follow-head">Follow us:</h3>
    <div class="social" aria-label="Social media links">
      <svg class="abs" style="left:0;top:0" width="57" height="10" aria-hidden="true"><line x1="8" y1="5" x2="50" y2="5" stroke="var(--green)" stroke-width=".6"/></svg>
      <span style="left:0"></span><span style="left:23.5px"></span><span style="left:47px"></span>
    </div>
    <p class="disclaimer">This material has been prepared for informational purposes only and is not intended to provide tax, accounting, or legal advice. Meadowlark and Allied Services is not a professional fiduciary organization. Please consult with your tax advisor or financial professional before making a decision about Smart Giving.</p>
  </div>

  <div class="panel panel--3">
    <div class="photo" style="left:0;top:85px;width:198px;height:340px;background:linear-gradient(170deg,#dcdde2 0%,#b8b4b4 35%,#8a3a35 62%,#5e2a2a 80%,#6c6461 100%)" role="img" aria-label="Photo of a woman in a red shawl looking at her phone outdoors"></div>
    <svg class="curve" width="198" height="460" viewBox="0 0 198 460" aria-hidden="true">
      <path d="M0 0 H198 V82 Q130 130 60 100 Q25 90 0 86 Z" fill="#ffffff"/>
      <path d="M15 85 Q50 95 80 106 Q140 125 198 82 V90 Q140 136 78 112 Q45 100 15 85 Z" fill="var(--green)"/>
      <path d="M0 418 Q80 368 198 390 V460 H0 Z" fill="var(--navy)"/>
      <path d="M0 430 Q85 380 198 398 V460 H0 Z" fill="#ffffff"/>
    </svg>
    <h1 class="cover-title">TRANSFORM YOUR GIVING</h1>
    <div class="cover-pill">BE STRATEGIC, BE SMART</div>
    <p class="cover-sub">Discover the impact of Smart Giving with<br>Meadowlark and Allied Services</p>

    <div class="bubble" style="left:14px;top:103px">
      <svg width="26" height="20" viewBox="0 0 26 20"><circle cx="8" cy="6" r="5" fill="none" stroke="var(--navy)" stroke-width="1.3"/><circle cx="18" cy="6" r="5" fill="none" stroke="var(--navy)" stroke-width="1.3"/><circle cx="13" cy="14" r="5" fill="#fff" stroke="var(--navy)" stroke-width="1.3"/></svg>Crypto</div>
    <div class="bubble" style="left:136px;top:147px">
      <svg width="22" height="20" viewBox="0 0 22 20"><circle cx="8" cy="8" r="5.5" fill="none" stroke="var(--navy)" stroke-width="1.6" stroke-dasharray="2 1.2"/><circle cx="15" cy="13" r="5" fill="none" stroke="var(--navy)" stroke-width="1.6" stroke-dasharray="2 1.2"/></svg>DAF's</div>
    <div class="bubble" style="left:14px;top:225px">
      <svg width="22" height="18" viewBox="0 0 22 18"><path d="M2 2V16H20" fill="none" stroke="var(--navy)" stroke-width="1.2"/><rect x="5" y="9" width="2.5" height="6" fill="var(--navy)"/><rect x="9" y="6" width="2.5" height="9" fill="var(--navy)"/><rect x="13" y="8" width="2.5" height="7" fill="var(--navy)"/><rect x="17" y="4" width="2.5" height="11" fill="var(--navy)"/></svg>Stocks &amp;<br>Securities</div>
    <div class="bubble" style="left:136px;top:254px">
      <svg width="22" height="22" viewBox="0 0 22 22"><rect x="3" y="8" width="16" height="4" fill="var(--navy)"/><rect x="4" y="12" width="14" height="9" fill="var(--navy)"/><rect x="10" y="8" width="2" height="13" fill="#fff"/><path d="M11 8C8 3 5 4 6.5 7M11 8C14 3 17 4 15.5 7" fill="none" stroke="var(--navy)" stroke-width="1.3"/></svg>QCDs</div>
    <div class="bubble" style="left:14px;top:322px">
      <svg width="22" height="20" viewBox="0 0 22 20"><g fill="var(--navy)"><rect x="6" y="16" width="8" height="2.2" rx="1"/><rect x="6" y="13" width="8" height="2.2" rx="1"/><rect x="11" y="10" width="8" height="2.2" rx="1"/><rect x="11" y="13" width="8" height="2.2" rx="1"/><rect x="11" y="16" width="8" height="2.2" rx="1"/><circle cx="16" cy="5" r="3.5"/></g><path d="M2 4h5M2 7h3" stroke="var(--navy)" stroke-width="1"/></svg>Charitable<br>Annuity</div>

    <div class="brand-name brand-name--cover"><span class="brand-dot"></span>Meadowlark and Allied Services</div>
  </div>
</section>

<!-- INSIDE SHEET -->
<section class="sheet sheet--inside">

  <div class="panel panel--1 panel--purple">
    <p class="copy" style="left:14px;top:15px">We would like to introduce you to five Strategic and Smart ways to give that could potentially be more beneficial to you compared to traditional cash donations. We encourage you to keep this information as a guide for your future contributions.</p>

    <div class="feature-head" style="left:14px;top:58px">
      <svg class="feature-icon" width="36" height="30" viewBox="0 0 36 30" aria-hidden="true"><path d="M1 3V28H35" fill="none" stroke="var(--green)" stroke-width="2"/><g fill="var(--green)"><rect x="7" y="17" width="4" height="9"/><rect x="13" y="12" width="4" height="14"/><rect x="19" y="15" width="4" height="11"/><rect x="25" y="9" width="4" height="17"/></g><path d="M6 12L14 6 20 10 30 2" fill="none" stroke="var(--green)" stroke-width="1.4"/></svg>
      <div>
        <div class="feature-title">Gifts of Stocks or Appreciated<br>Assets Strategic &amp; Smart</div>
        <div class="feature-tag">Consider your long-term publicly traded stock as a way to give to your favorite charity.</div>
      </div>
    </div>
    <p class="copy" style="left:14px;top:105px">You can make a significantly bigger impact when you donate long-term appreciated securities, including stock, mutual funds, and bonds, directly to your favorite charity.</p>
    <div class="how-pill" style="left:13px;top:136px">HOW DOES IT WORK?</div>
    <p class="copy" style="left:13px;top:162px">When you donate stock to a charity, you will generally take a tax deduction for the full market value. Because you are donating stock, your contribution and tax deduction may be significantly higher than contributing the after-tax proceeds. The same benefits apply when you donate mutual funds or bonds.</p>

    <div class="feature-head" style="left:14px;top:223px">
      <svg class="feature-icon" width="36" height="34" viewBox="0 0 36 34" aria-hidden="true"><circle cx="13" cy="13" r="9" fill="none" stroke="var(--green)" stroke-width="2.4" stroke-dasharray="3 1.6"/><circle cx="13" cy="13" r="4" fill="none" stroke="var(--green)" stroke-width="1.4"/><circle cx="24" cy="23" r="8" fill="none" stroke="var(--green)" stroke-width="2.4" stroke-dasharray="3 1.6"/><circle cx="24" cy="23" r="3.5" fill="none" stroke="var(--green)" stroke-width="1.4"/></svg>
      <div>
        <div class="feature-title">Donor-Advised Fund (DAF)<br>Strategic &amp; Smart</div>
        <div class="feature-tag">Consider a DAF – a simple, flexible, and tax-advantageous way to give to your favorite charities.</div>
      </div>
    </div>
    <p class="copy" style="left:14px;top:269px">A Donor-Advised Fund (DAF), is like a charitable investment account for the sole purpose of supporting your favorite charities.</p>
    <div class="how-pill" style="left:13px;top:300px">HOW DOES IT WORK?</div>
    <p class="copy" style="left:13px;top:325px">You establish a DAF and contribute cash, stocks, or non-publicly traded assets, cryptocurrency, and private company stock to be eligible for an immediate tax deduction. Those funds are contributed for tax-free growth. You can recommend grants be made from your DAF to any IRS qualified public charity.</p>

    <div class="photo" style="left:0;top:375px;width:199px;height:85px;background:linear-gradient(120deg,#6b5a4e 0%,#a89384 40%,#d8cabd 75%,#efe6dc 100%)" role="img" aria-label="Photo of a worried older woman holding her forehead"></div>
    <svg class="curve" style="top:375px" width="199" height="85" viewBox="0 0 199 85" aria-hidden="true">
      <path d="M0 0 H199 V85 Q130 20 0 18 Z" fill="#2c2377"/>
      <path d="M0 18 Q130 20 199 85 H192 Q125 28 0 25 Z" fill="var(--green)"/>
      <path d="M192 85 Q125 28 0 25 V28 Q122 32 188 85 Z" fill="#ffffff"/>
    </svg>
  </div>

  <div class="panel panel--2 panel--white" style="background:#fff">
    <div class="photo" style="left:0;top:0;width:199px;height:236px;background:linear-gradient(165deg,#6f8e56 0%,#a7b59a 30%,#cfc8c0 55%,#8d6f65 80%,#eef1f2 100%)" role="img" aria-label="Photo of a stressed mother reviewing bills while holding her child"></div>
    <div class="feature-head" style="left:13px;top:253px">
      <svg class="feature-icon" width="30" height="36" viewBox="0 0 30 36" aria-hidden="true"><rect x="1" y="11" width="28" height="7" fill="var(--green)"/><rect x="3" y="19" width="24" height="16" fill="var(--green)"/><rect x="13" y="11" width="4" height="24" fill="#fff"/><path d="M15 11C11 2 5 3 7 9M15 11C19 2 25 3 23 9" fill="none" stroke="var(--green)" stroke-width="2.2"/></svg>
      <div>
        <div class="feature-title">Qualified Charitable Distributions<br>(QCDs) Strategic &amp; Smart</div>
        <div class="feature-tag">Consider a QCD – when planning your IRA withdrawal strategy...and donate to your favorite charity.</div>
      </div>
    </div>
    <p class="copy" style="left:13px;top:304px;width:176px">IRA owners at age 70 or over can transfer dollars from their IRA to charity tax-free each year. These transfers known as Qualified Charitable Distributions (QCDs) offer eligible older Americans a great way to easily give to charity.</p>
    <div class="how-pill" style="left:12px;top:350px">HOW DOES IT WORK?</div>
    <p class="copy" style="left:13px;top:372px;width:176px">Are you 72 and required to take a minimum distribution (RMD) from your IRA but do not need the funds? Consider a Qualified Charitable Distribution. Normally, distributions from a traditional IRA are taxable when received. With a QCD, these distributions become tax-free when paid directly from the IRA to your favorite eligible charity. An IRA owner wishing to make a QCD should contact their IRA trustee, allowing time to complete the transaction before the end of the year to receive the tax benefit.</p>
  </div>

  <div class="panel panel--3 panel--purple">
    <div class="feature-head" style="left:16px;top:13px">
      <svg class="feature-icon" width="30" height="26" viewBox="0 0 30 26" aria-hidden="true"><circle cx="9" cy="8" r="6.5" fill="none" stroke="var(--green)" stroke-width="1.8"/><circle cx="21" cy="8" r="6.5" fill="none" stroke="var(--green)" stroke-width="1.8"/><circle cx="15" cy="18" r="6.5" fill="#332a86" stroke="var(--green)" stroke-width="1.8"/></svg>
      <div>
        <div class="feature-title">Cryptocurrency Strategic &amp; Smart</div>
        <div class="feature-tag">Consider donating Bitcoin and other<br>cryptocurrencies to your favorite charity.</div>
      </div>
    </div>
    <p class="copy" style="left:14px;top:52px">Bitcoin and other cryptocurrencies can be donated to charity just like other appreciated assets such as stocks and other business interests. Before you sell bitcoin and donate the after-tax proceeds, consider donating your bitcoin directly to a favorite charity.</p>
    <div class="how-pill" style="left:13px;top:95px">HOW DOES IT WORK?</div>
    <p class="copy" style="left:14px;top:114px">Many donors find it useful to open a Donor-Advised Fund (DAF). This strategy includes two significant benefits, both for you and your favorite charity.</p>
    <ul class="bullets" style="top:151px">
      <li><span class="tick"></span><span>Your tax deduction will be equal to the fair market value of the donated bitcoin (as determined by a qualified appraisal).</span></li>
      <li><span class="tick"></span><span>Your cryptocurrency donation is tax-smart because it may eliminate capital gains taxes on the value /appreciation AND your favorite charity will receive 100% of the value of the contribution.</span></li>
    </ul>
    <p class="copy" style="left:14px;top:217px">Often charities are not able to accept direct donations of bitcoin/crypto so using a DAF is a great way to donate these assets.</p>

    <div class="feature-head" style="left:14px;top:250px">
      <svg class="feature-icon" width="32" height="30" viewBox="0 0 32 30" aria-hidden="true"><g fill="var(--green)"><rect x="2" y="24" width="11" height="3" rx="1.5"/><rect x="2" y="20" width="11" height="3" rx="1.5"/><rect x="14" y="24" width="11" height="3" rx="1.5"/><rect x="14" y="20" width="11" height="3" rx="1.5"/><rect x="14" y="16" width="11" height="3" rx="1.5"/><circle cx="22" cy="7" r="5.5"/></g><path d="M1 4h8M1 8h5" stroke="var(--green)" stroke-width="1.4"/></svg>
      <div>
        <div class="feature-title">Charitable Gift Annuity<br>Strategic &amp; Smart</div>
        <div class="feature-tag">Consider establishing a Charitable<br>Gift Annuity</div>
      </div>
    </div>
    <p class="copy" style="left:14px;top:290px">You make a donation to a single charity. The gift is set aside in a reserve account and invested.</p>
    <div class="how-pill" style="left:13px;top:312px">HOW DOES IT WORK?</div>
    <p class="copy" style="left:14px;top:335px">A charitable gift annuity is a contract between a donor and a charity. As a donor, you make a sizable gift to charity using cash, securities, or possibly other assets. This money is then invested. In return, you become eligible to take a partial tax deduction for your donation, plus you receive a fixed stream of income from the charity for the rest of your life. At the end of your life (as well as your spouse's, if you're giving as a couple), the charity receives the remainder of the gift.</p>

    <svg class="curve" style="top:405px" width="198" height="55" viewBox="0 0 198 55" aria-hidden="true">
      <path d="M0 55 Q40 5 198 8 V55 Z" fill="#ffffff"/>
      <path d="M0 55 Q40 5 198 8 V0 Q40 -3 0 55 Z" fill="var(--green)"/>
      <path d="M0 55 Q42 14 198 18 V55 Z" fill="#2c2377"/>
    </svg>
    <div class="url-pill">www.meadowlarkallied.org</div>
  </div>
</section>

</body>
</html>
```